sydney wedding photography business needs a business card design

we need a business card design for a sydney based wedding photography and videography business. our business name is :golden hour studio and film. our target clients are 24-35 yrs female. our style is candid, organic, natural, dynamic. we are a team of young photographers and videographers, and help brides to create memories that they will cherish for the rest of their lives. the logo will be provided. we want an elegant design that reflects our style, and also want to give a great impression to our clients that we are one of the best studios in sydney and our brand means quality and premium service.

Target Market(s)

bride to be, 24-35 years old, living in sydney and surrunding areas

Industry/Entity Type

Wedding Photography

Contact Information for Business Card

address: 57 tarrant street, glenmore nsw 2047
mobile: 0431872259
phone: (02) 9163 2408
info@tidewillowstudio.net.au
www.tidewillowstudio.net.au
facebook:tidewillowweddings
instagram:tidewillowweddings

Font styles to use
Serif
Sans Serif

Requirements
Nice to have
• maybe add my slogan"memories beyond eternity" if the layout looks good
Should not have
• no black color, not good idea for wedding biz card

```html
<!DOCTYPE html>
<html lang="en">
<head>
<meta charset="utf-8">
<title>golden hour studio and film – business card</title>
<link rel="stylesheet" href="https://fonts.googleapis.com/css2?family=Open+Sans:wght@400;600;700&display=swap">
<style>
  :root {
    --backdrop: #ecebe8;
    --card-white: #ffffff;
    --gold: #f5c102;
    --gold-deep: #daa70d;
    --gold-pattern: #e9b300;
    --logo-gold: #d4a20c;
    --ink: #2e2611;
    --on-gold: #ffffff;
  }
  * { box-sizing: border-box; margin: 0; padding: 0; }
  html, body { width: 1200px; height: 900px; overflow: hidden; }
  body {
    background: var(--backdrop);
    font-family: "Open Sans", Arial, sans-serif;
    color: var(--ink);
    position: relative;
  }
  .card {
    position: absolute;
    overflow: hidden;
    box-shadow: 0 6px 18px rgba(60, 50, 20, 0.18);
  }
  /* Front */
  .card-front {
    left: 78px; top: 34px; width: 588px; height: 364px;
    background: var(--card-white);
  }
  .front-bands { position: absolute; inset: 0; }
  .front-brand {
    position: absolute; left: 0; right: 0; top: 74px;
    text-align: center;
    font-size: 33px; font-weight: 600;
    color: var(--logo-gold);
    letter-spacing: 0.5px;
  }
  .person {
    position: absolute; right: 316px; top: 246px;
    text-align: right;
  }
  .person-name { font-size: 19px; font-weight: 700; line-height: 24px; }
  .person-role { font-size: 15px; line-height: 22px; }
  .contact-list {
    position: absolute; left: 292px; top: 236px;
    list-style: none;
  }
  .contact-item {
    display: flex; align-items: center;
    height: 21px; font-size: 15px;
  }
  .contact-icon { width: 12px; height: 12px; margin-right: 14px; flex: none; }
  .address {
    position: absolute; left: 104px; top: 313px;
    font-size: 15px;
  }
  /* Back */
  .card-back {
    left: 388px; top: 505px; width: 567px; height: 352px;
    background: var(--gold);
  }
  .back-pattern {
    position: absolute; inset: 0;
    background: linear-gradient(135deg, var(--gold) 0%, var(--gold-pattern) 50%, var(--gold) 100%);
  }
  .back-brand {
    position: absolute; left: 0; right: 0; top: 148px;
    text-align: center;
    font-size: 30px; font-weight: 600;
    color: var(--on-gold);
  }
  .social-row {
    position: absolute; left: 0; right: 0; top: 277px;
    display: flex; justify-content: center; gap: 9px;
  }
  .social-tile {
    width: 27px; height: 27px; border-radius: 4px;
    background: var(--on-gold);
  }
</style>
</head>
<body>
  <section class="card card-front">
    <svg class="front-bands" width="588" height="364" viewBox="0 0 588 364" aria-hidden="true">
      <path d="M0 185 H400 L380 210 H0 Z" fill="var(--gold-deep)"/>
      <path d="M0 214 H386 L416 177 H588 V364 H0 Z" fill="var(--gold)"/>
    </svg>
    <div class="front-brand">golden hour studio and film</div>
    <div class="person">
      <div class="person-name">Oliver Bennett</div>
      <div class="person-role">Managing Director</div>
    </div>
    <ul class="contact-list">
      <li class="contact-item">
        <svg class="contact-icon" viewBox="0 0 12 12"><path d="M2.5 0.5 L4.5 3 L3.4 4.4 C4 5.9 5.8 7.8 7.6 8.6 L9 7.5 L11.5 9.5 L10.3 11.3 C5.5 11 1 6.5 0.7 1.7 Z" fill="var(--ink)"/></svg>
        <span>0431872259</span>
      </li>
      <li class="contact-item">
        <svg class="contact-icon" viewBox="0 0 12 12"><rect x="1" y="2.5" width="10" height="7" fill="var(--ink)"/><path d="M1.5 3 L6 6.5 L10.5 3" stroke="var(--gold)" stroke-width="1" fill="none"/></svg>
        <span>info@tidewillowstudio.net.au</span>
      </li>
      <li class="contact-item">
        <svg class="contact-icon" viewBox="0 0 12 12"><circle cx="6" cy="6" r="5" fill="var(--ink)"/><path d="M1 6 H11 M6 1 C3.5 3.5 3.5 8.5 6 11 M6 1 C8.5 3.5 8.5 8.5 6 11" stroke="var(--gold)" stroke-width="0.8" fill="none"/></svg>
        <span>www.tidewillowstudio.net.au</span>
      </li>
    </ul>
    <p class="address">57 tarrant street, glenmore nsw 2047</p>
  </section>

  <section class="card card-back">
    <div class="back-pattern" role="img" aria-label="Repeating faint gem pattern in darker gold across the card"></div>
    <div class="back-brand">golden hour studio and film</div>
    <div class="social-row">
      <span class="social-tile"></span>
      <span class="social-tile"></span>
      <span class="social-tile"></span>
      <span class="social-tile"></span>
    </div>
  </section>
</body>
</html>
```